Ecommerce site that acts also as a portal for B2C members and non- members and B2B. Please see attachment this is for only front end work, backend will follow. Husk and Kettle- a MRVL Hospitality Company

Products
Coffee bean sourcing, acquisition, roasting, grinding, blending, sale/delivery
Tea sourcing, acquisition, roasting, grinding, blending, sale/delivery
Applicable/Associated Merchandise and Accoutrements

Initial market penetration for both B2C and B2B offering Husk and Kettle custom blends of both Coffees and Teas.
B2C- Zelvora style sale/distribution via guest and members. Members initial fee $129 annual $99 a year thereafter with benefits such as 1st year gift of a French Press Travel Mug (customized/logo/name/brand), monthly samples. Attached document has non project related information for narrative and conceptual inputs.

Coding

```html
<!DOCTYPE html>
<html lang="en">
<head>
<meta charset="utf-8">
<title>Husk and Kettle — Artisan Coffee and Tea</title>
<link href="https://fonts.googleapis.com/css2?family=Marcellus&family=Poppins:wght@300;400;500&display=swap" rel="stylesheet">
<style>
:root{
  --accent:#b07d45;
  --accent-dark:#9a6a36;
  --ink:#2b2420;
  --muted:#777;
  --brown-deep:#3b2213;
  --brown-mid:#6a3f22;
  --paper:#ffffff;
  --stone:#e8e7e5;
  --mist:#f2f1f0;
  --line:#d9d6d2;
}
*{margin:0;padding:0;box-sizing:border-box}
html,body{width:1200px;height:4563px;overflow:hidden}
body{font-family:"Poppins",sans-serif;color:var(--ink);background:var(--paper);position:relative}
.serif{font-family:"Marcellus",serif;font-weight:400}
section,header,footer{position:relative;width:1200px;overflow:hidden}
.abs{position:absolute}
.btn{position:absolute;display:flex;align-items:center;justify-content:center;background:var(--accent);color:#fff;border-radius:20px;font-size:11px;font-family:"Poppins",sans-serif}
.center{text-align:center;left:0;width:1200px}

/* header */
.site-header{height:67px;background:#fff}
.brand{position:absolute;left:117px;top:21px;display:flex;align-items:center;gap:8px;font-family:"Poppins",sans-serif;font-weight:500;font-size:14px;color:var(--ink);letter-spacing:.2px}
.brand-dot{width:20px;height:20px;border-radius:50%;background:var(--accent)}
.main-nav{position:absolute;left:416px;top:26px;display:flex;gap:20px;font-size:10px;color:#444}
.main-nav .active{color:var(--accent);text-decoration:underline}
.nav-icons{position:absolute;left:978px;top:23px;display:flex;gap:25px;align-items:center}
.nav-icons .sep{width:1px;height:18px;background:var(--line);margin:0 -12px}

/* hero */
.hero{height:669px;background:radial-gradient(ellipse 420px 260px at 820px 300px,#c49a6c 0%,#8a5a34 35%,transparent 70%),radial-gradient(ellipse 500px 200px at 700px 560px,#4a2a15 0%,transparent 80%),linear-gradient(90deg,#120a06 0%,#2a170c 40%,#5a3519 75%,#3a2010 100%)}
.hero-rule{left:122px;top:185px;width:3px;height:175px;background:var(--accent)}
.hero h1{left:135px;top:178px;font-size:58px;line-height:58px;color:#fff;width:560px}
.hero p{left:135px;top:362px;font-size:11px;line-height:16px;color:#eee;width:330px}

/* club */
.club{height:359px;background:var(--stone)}
.club-photo{left:170px;top:64px;width:410px;height:230px;border-radius:50%;background:radial-gradient(ellipse at 45% 40%,#f4efe8 0%,#d9c3a5 22%,#6b3d1e 40%,#3e2212 60%,transparent 72%)}
.club h2{left:641px;top:106px;font-size:28px;color:var(--ink)}
.club p{left:641px;top:158px;width:380px;font-size:11px;line-height:19px;color:#666}

/* signature */
.signature{height:562px;background:#fff}
.signature h2{top:68px;font-size:32px}
.signature .lede{top:118px;font-size:10.5px;line-height:17px;color:#555}
.blend-card{position:absolute;top:178px;width:220px;text-align:center}
.blend-photo{width:185px;height:185px;border-radius:50%;margin:0 auto}
.blend-card h3{font-family:"Marcellus",serif;font-weight:400;font-size:14px;line-height:17px;margin-top:18px;color:var(--ink)}
.blend-card .price{font-size:12px;color:#888;margin-top:20px}

/* luxury */
.luxury{height:647px;background:#fff}
.luxury h2{top:30px;font-size:26px}
.luxury .lede{top:80px;font-size:10.5px;line-height:18px;color:#777}
.video{left:117px;top:163px;width:962px;height:458px;background:radial-gradient(ellipse 200px 150px at 480px 190px,#e8c89a 0%,#b9844c 35%,transparent 75%),radial-gradient(ellipse 300px 180px at 200px 300px,#5a2e14 0%,transparent 80%),linear-gradient(135deg,#3b1d0c 0%,#6b3a1b 45%,#2a140a 100%)}
.play{left:437px;top:172px;width:96px;height:96px;border-radius:50%;background:#fff;display:flex;align-items:center;justify-content:center}

/* steps */
.steps{height:355px;background:#fff}
.steps h2{top:52px;font-size:24px}
.steps .lede{top:94px;font-size:10px;color:#555}
.step{position:absolute;top:148px;width:220px;text-align:center}
.step-icon{width:64px;height:64px;margin:0 auto;display:flex;align-items:center;justify-content:center}
.step h3{font-family:"Marcellus",serif;font-weight:400;font-size:13px;margin-top:28px}
.step p{font-size:8.5px;line-height:13px;color:#777;margin-top:10px}
.divider{left:117px;bottom:0;width:965px;height:1px;background:var(--line)}

/* wholesale */
.wholesale{height:505px;background:#fff}
.wholesale h2{left:213px;top:128px;font-size:26px;line-height:31px;width:340px}
.wholesale p{left:213px;top:226px;width:350px;font-size:10px;line-height:18px;color:#666}
.splash{left:660px;top:60px;width:310px;height:340px;background:radial-gradient(ellipse 130px 150px at 50% 42%,#5a2e14 0%,#8b5a32 35%,#e9e3dc 60%,transparent 75%)}

/* member */
.member{height:429px;background:linear-gradient(90deg,#2a160b 0%,#3f2413 60%,#2d170a 100%)}
.member-photo{left:0;top:0;width:640px;height:429px;background:radial-gradient(ellipse 190px 140px at 360px 200px,#e7dccd 0%,#b88a5c 30%,transparent 70%),linear-gradient(100deg,#3a1e0e 0%,#6b3d1f 45%,#3b2213 100%)}
.member h2{left:686px;top:78px;font-size:36px;line-height:42px;color:#fff;width:400px}
.member p{left:686px;top:178px;width:345px;font-size:10px;line-height:16px;color:#eee}

/* testimonials */
.testimonials{height:422px;background:var(--mist)}
.testimonials h2{top:72px;font-size:26px}
.quote-mark{top:108px;font-size:110px;line-height:110px;color:var(--accent)}
.quote{top:210px;font-size:16px;line-height:24px;color:#888;font-weight:300}
.cite{top:273px;font-size:12px;color:#888;letter-spacing:.5px}
.dots{left:580px;top:328px;display:flex;gap:8px}
.dots span{width:8px;height:8px;border-radius:50%;background:#bbb}
.dots .on{background:var(--accent)}

/* footer */
.site-footer{height:500px;background:#e6e5e3}
.site-footer h2{top:65px;font-size:30px}
.site-footer .lede{top:112px;font-size:10.5px;color:#555}
.subscribe-input{left:267px;top:140px;width:545px;height:40px;background:#dcdad7;font-size:10px;color:#888;padding:13px 20px}
.subscribe-btn{left:812px;top:140px;width:123px;height:40px;background:var(--accent);color:#fff;font-size:11px;display:flex;align-items:center;justify-content:center}
.footer-brand{left:178px;top:283px;display:flex;align-items:center;gap:14px;font-family:"Marcellus",serif;font-size:28px;color:var(--ink)}
.footer-brand .brand-dot{width:42px;height:42px}
.col{position:absolute;top:245px}
.col h4{font-family:"Marcellus",serif;font-weight:400;font-size:17px;margin-bottom:14px}
.col li{list-style:none;font-size:9.5px;color:#666;line-height:18.5px}
.contact li{display:flex;gap:8px;line-height:13px;margin-bottom:14px}
.copyright{height:48px;background:var(--brown-deep);color:#eee;font-size:10px;display:flex;align-items:center;justify-content:center}
.to-top{left:1115px;top:4480px;width:40px;height:40px;background:var(--accent);display:flex;align-items:center;justify-content:center}
</style>
</head>
<body>

<header class="site-header">
  <div class="brand"><span class="brand-dot"></span>HUSK AND KETTLE</div>
  <nav class="main-nav">
    <span class="active">Home</span><span>Shop</span><span>Custom Blends</span><span>Membership</span><span>Wholesale</span><span>About Us</span><span>Blog / Recipes</span><span>Contact</span>
  </nav>
  <div class="nav-icons">
    <svg width="14" height="16" viewBox="0 0 14 16" fill="none" stroke="#333" stroke-width="1.3"><path d="M2 5h10l-1 10H3z"/><path d="M4.5 5V3.5a2.5 2.5 0 0 1 5 0V5"/></svg>
    <span class="sep"></span>
    <svg width="15" height="15" viewBox="0 0 15 15" fill="none" stroke="#333" stroke-width="1.3"><circle cx="7.5" cy="5" r="3.2"/><path d="M1.5 14c.8-3 3.2-4.5 6-4.5s5.2 1.5 6 4.5"/></svg>
    <span class="sep"></span>
    <svg width="15" height="15" viewBox="0 0 15 15" fill="none" stroke="#333" stroke-width="1.4"><circle cx="6.5" cy="6.5" r="5"/><path d="M10.2 10.2L14 14"/></svg>
  </div>
</header>

<section class="hero" role="img" aria-label="Latte with leaf art in a white cup on burlap, surrounded by roasted coffee beans">
  <div class="abs hero-rule"></div>
  <h1 class="abs serif">Artisan Coffee and Tea, Crafted for Connoisseurs</h1>
  <p class="abs">Explore exclusive blends, premium teas, and custom roasts curated for taste, aroma, and sophistication.</p>
  <span class="btn" style="left:135px;top:423px;width:120px;height:38px">Shop Now</span>
</section>

<section class="club">
  <div class="abs club-photo" role="img" aria-label="Cup of coffee on a saucer with a spoon, scattered coffee beans"></div>
  <h2 class="abs serif">Join The Husk and Kettle Club</h2>
  <p class="abs">Become a member for $129 the first year, $99 thereafter, and enjoy exclusive perks including a customized French Press Travel Mug and monthly sample blends.</p>
  <span class="btn" style="left:641px;top:234px;width:107px;height:33px;font-size:10px">Join Now</span>
</section>

<section class="signature">
  <h2 class="abs center serif">Create Your Signature Blend</h2>
  <p class="abs center lede">Choose from premium origins, select your roast level, and craft a unique<br>coffee or tea blend tailored to your taste.</p>
  <div class="blend-card" style="left:233px">
    <div class="blend-photo" role="img" aria-label="Ground espresso in a portafilter on a wooden table" style="background:radial-gradient(circle at 45% 55%,#5a3018 0%,#8a5a34 40%,#3a2416 100%)"></div>
    <h3>Single Origin, Espresso,<br>Custom Roast</h3>
    <p class="price">Starting from: $XX</p>
  </div>
  <div class="blend-card" style="left:490px">
    <div class="blend-photo" role="img" aria-label="Loose tea leaves, herbs and a green apple on a dark surface" style="background:radial-gradient(circle at 60% 40%,#5c8a3a 0%,#2d3b25 35%,#1b1b1b 70%,#3a2418 100%)"></div>
    <h3>Herbal, Green, Black,<br>Seasonal</h3>
    <p class="price">Starting from: $XX</p>
  </div>
  <div class="blend-card" style="left:747px">
    <div class="blend-photo" role="img" aria-label="French press pouring coffee into a travel mug outdoors" style="background:linear-gradient(160deg,#c7d3da 0%,#b89a78 45%,#5a3a22 75%,#2e2218 100%)"></div>
    <h3>French Press, Travel Mugs,<br>Brewing Equipment</h3>
    <p class="price">Starting from: $XX</p>
  </div>
  <span class="btn" style="left:530px;top:481px;width:140px;height:36px;font-size:10px">View All Products</span>
</section>

<section class="luxury">
  <h2 class="abs center serif">Luxury in Every Sip</h2>
  <p class="abs center lede">Husk and Kettle, a MRVL Hospitality Company, sources the finest coffee beans and tea leaves worldwide. From<br>meticulous roasting to expert blending, we craft unique flavors for both discerning individuals and business partners.<br>Our passion for quality ensures every cup tells a story of refinement, aroma, and indulgence.</p>
  <div class="abs video" role="img" aria-label="Video still of a coffee cup on a saucer among roasted beans on a wooden table">
    <div class="abs play"><svg width="18" height="20" viewBox="0 0 18 20"><path d="M2 1l15 9-15 9z" fill="#222"/></svg></div>
  </div>
</section>

<section class="steps">
  <h2 class="abs center serif">Your Blend, Your Way</h2>
  <p class="abs center lede">Select your beans, roast, and flavor notes for a coffee or tea experience that’s truly yours.</p>
  <div class="step" style="left:228px">
    <div class="step-icon" style="background:var(--accent)"><svg width="32" height="32" viewBox="0 0 32 32" fill="none" stroke="#fff" stroke-width="1.5"><path d="M16 28V10"/><path d="M16 14c-4 0-7-3-7-7 4 0 7 3 7 7z"/><path d="M16 18c4 0 7-3 7-7-4 0-7 3-7 7z"/><path d="M6 28h20"/></svg></div>
    <h3>Choose Beans or Leaves</h3>
    <p>Pick from our premium single-origin coffees or<br>hand-selected teas for a rich, authentic taste.</p>
  </div>
  <div class="step" style="left:488px">
    <div class="step-icon" style="background:var(--brown-deep)"><svg width="32" height="32" viewBox="0 0 32 32" fill="none" stroke="#fff" stroke-width="1.5"><path d="M11 4c-1 2 1 3 0 5M16 4c-1 2 1 3 0 5M21 4c-1 2 1 3 0 5"/><path d="M5 24h22"/><path d="M8 24a8 8 0 0 1 16 0"/><path d="M13 28h6"/></svg></div>
    <h3>Select Roast or Steep Style</h3>
    <p>Customize the roast level or tea steeping style to<br>match your flavor preference.</p>
  </div>
  <div class="step" style="left:751px">
    <div class="step-icon" style="background:var(--accent)"><svg width="32" height="32" viewBox="0 0 32 32" fill="none" stroke="#fff" stroke-width="1.5"><rect x="6" y="12" width="20" height="15"/><rect x="4" y="8" width="24" height="5"/><path d="M16 8v19"/><path d="M16 8c-3 0-6-2-4-4s4 2 4 4c0-2 2-6 4-4s-1 4-4 4"/></svg></div>
    <h3>Customize Gift Options</h3>
    <p>Add your personal touch with custom packaging,<br>gift wrapping, or branded accessories.</p>
  </div>
  <div class="abs divider"></div>
</section>

<section class="wholesale">
  <h2 class="abs serif">Wholesale &amp; Corporate Partnerships</h2>
  <p class="abs">Our B2B program provides premium blends, flexible bulk ordering, and tailored solutions for cafes, restaurants, and hospitality businesses. Elevate your brand with exclusive artisan products.</p>
  <span class="btn" style="left:213px;top:291px;width:180px;height:35px;font-size:10px">Request Wholesale Pricing</span>
  <div class="abs splash" role="img" aria-label="Coffee splashing from a tilted cup on a saucer full of beans"></div>
</section>

<section class="member">
  <div class="abs member-photo" role="img" aria-label="Steaming coffee cup on a saucer beside a burlap sack of beans"></div>
  <h2 class="abs serif">Become a Husk and Kettle Member</h2>
  <p class="abs">Enjoy exclusive perks as a member: monthly samples, early access to new blends, and a complimentary French Press Travel Mug in your first year. Membership starts at $129 the first year and $99 annually thereafter.</p>
  <span class="btn" style="left:686px;top:256px;width:148px;height:35px;font-size:10px">About Membership</span>
</section>

<section class="testimonials">
  <h2 class="abs center serif">What Our Customers Say</h2>
  <div class="abs center serif quote-mark">“</div>
  <p class="abs center quote">The aroma and taste are unmatched. My mornings<br>have never been the same.</p>
  <p class="abs center cite">- MARA ELLISON</p>
  <div class="abs dots"><span></span><span class="on"></span><span></span></div>
</section>

<footer class="site-footer">
  <h2 class="abs center serif">Join the Kettlewood Family</h2>
  <p class="abs center lede">Get updates on our weekly deals and seasonal specials. We promise you’ll love our emails</p>
  <div class="abs subscribe-input">Enter your email address</div>
  <div class="abs subscribe-btn">Subscribe</div>
  <div class="abs footer-brand"><span class="brand-dot"></span>Husk and Kettle</div>
  <div class="col" style="left:546px">
    <h4>Quick Links</h4>
    <ul><li>Home</li><li>Shop</li><li>Custom Blends</li><li>Membership</li><li>Wholesale</li><li>About Us</li><li>Blog / Recipes</li><li>Contact</li></ul>
  </div>
  <div class="col" style="left:704px">
    <h4>Information</h4>
    <ul><li>Search</li><li>About us</li><li>Locations &amp; Menu</li><li>Refund Policy</li><li>Privacy Policy</li></ul>
  </div>
  <div class="col contact" style="left:863px">
    <h4>Contact Us</h4>
    <ul>
      <li><svg width="10" height="8" viewBox="0 0 10 8"><rect width="10" height="8" fill="var(--accent)"/><path d="M0 0l5 4 5-4" stroke="#fff" fill="none"/></svg><span>Email:<br>support@huskandkettle.com</span></li>
      <li><svg width="10" height="10" viewBox="0 0 10 10"><path d="M2 0l2 2-1 2c1 1 2 2 3 3l2-1 2 2-2 2C4 10 0 6 0 2z" fill="var(--accent)"/></svg><span>Phone:<br>+1 0000 XXX-XXXX</span></li>
      <li><svg width="9" height="12" viewBox="0 0 9 12"><path d="M4.5 0A4.5 4.5 0 0 0 0 4.5C0 8 4.5 12 4.5 12S9 8 9 4.5A4.5 4.5 0 0 0 4.5 0z" fill="var(--accent)"/><circle cx="4.5" cy="4.5" r="1.6" fill="#e6e5e3"/></svg><span>Address:<br>123 Coffee Street, City, State, Zip</span></li>
    </ul>
  </div>
</footer>

<div class="abs to-top"><svg width="12" height="14" viewBox="0 0 12 14" fill="none" stroke="#fff" stroke-width="1.4"><path d="M6 13V1M1 6l5-5 5 5"/></svg></div>

<div class="copyright">© Copyright 2026 Husk &amp; Kettle. All right reserved</div>

</body>
</html>
```